Salon and Spa Distributor Business Card

Need a business card. We are are distributor in the salon and spa industry. We identify with natural beauty. Need a card with:
Company Name: Petal Quarry"
Title: "President & CEO"
Address
Company Phone number
email
website
Tag Line:" The Professional Salon Source"

Industry/Entity Type

Business

Contact Information for Business Card

Name: Dov Strommen
Title: "President & CEO"
Address: 31 Harlow Ln, Bexmoor, NJ 07813
Company Phone number: 800-463-5918
email: dovstrommen@petalquarry.example
website: www.petalquarry.example

Requirements
Should not have
• No black backgrounds

```html
<!DOCTYPE html>
<html lang="en">
<head>
<meta charset="utf-8">
<title>Petal Quarry — Business Card</title>
<link rel="stylesheet" href="https://fonts.googleapis.com/css2?family=Questrial&display=swap">
<style>
  :root {
    --page-bg: #e8e8e8;
    --green-deep: #00602a;
    --green-mid: #1f7a35;
    --green-soft: #348b45;
    --green-bright: #3fae3a;
    --green-light: #5cc447;
    --card-white: #f8f8f8;
    --text-dark: #2b2b2b;
    --white: #ffffff;
  }
  * { margin: 0; padding: 0; box-sizing: border-box; }
  html, body {
    width: 1200px; height: 576px; overflow: hidden;
    background: var(--page-bg);
    font-family: "Questrial", "Century Gothic", sans-serif;
  }
  .canvas { position: relative; width: 1200px; height: 576px; }

  .card {
    position: absolute; top: 138px;
    width: 484px; height: 294px;
    border-radius: 13px; overflow: hidden;
    box-shadow: 0 2px 6px rgba(0,0,0,0.18);
  }

  /* Front */
  .card-front {
    left: 82px;
    background: linear-gradient(180deg, var(--green-deep) 0%, var(--green-soft) 100%);
  }
  .front-mark {
    position: absolute; left: 206px; top: 80px;
    width: 72px; height: 72px; border-radius: 50%;
    background: rgba(255,255,255,0.9);
  }
  .front-name {
    position: absolute; left: 0; right: 0; top: 190px;
    text-align: center; color: var(--white);
    font-size: 27px; letter-spacing: 0.2px;
  }

  /* Back */
  .card-back { left: 602px; background: var(--card-white); }
  .accent-bar {
    position: absolute; left: 0; top: 31px;
    width: 12px; height: 47px; background: var(--green-soft);
  }
  .company-name {
    position: absolute; left: 26px; top: 35px;
    font-size: 24px; color: var(--green-mid);
  }
  .job-title {
    position: absolute; left: 26px; top: 63px;
    font-size: 10.5px; color: var(--green-mid);
  }
  .back-mark {
    position: absolute; left: 326px; top: 34px;
    width: 128px; height: 128px; border-radius: 50%;
    background: linear-gradient(160deg, var(--green-light), var(--green-bright));
  }
  .contact-list {
    position: absolute; left: 26px; top: 188px;
    list-style: none; font-size: 13px; color: var(--text-dark);
  }
  .contact-list li {
    display: flex; align-items: center; height: 18px;
  }
  .contact-list svg { width: 11px; height: 11px; margin: 0 12px 0 5px; fill: var(--green-mid); }
  .contact-list .address { margin-top: 2px; }

  .footer-band { position: absolute; left: 0; bottom: 0; width: 484px; height: 42px; }
  .tagline {
    position: absolute; right: 20px; bottom: 10px;
    font-size: 13px; color: var(--white);
  }
</style>
</head>
<body>
<main class="canvas">

  <section class="card card-front" aria-label="Card front">
    <div class="front-mark"></div>
    <div class="front-name">Petal Quarry</div>
  </section>

  <section class="card card-back" aria-label="Card back">
    <div class="accent-bar"></div>
    <div class="company-name">Petal Quarry</div>
    <div class="job-title">President &amp; CEO</div>
    <div class="back-mark"></div>

    <ul class="contact-list">
      <li>
        <svg viewBox="0 0 12 12"><path d="M1 3.5C1 2.4 2.5 1.5 6 1.5s5 .9 5 2v1.2H8.6V3.6H3.4v1.1H1z"/><path d="M3 5h6l1.5 5.5h-9z"/><circle cx="6" cy="7.6" r="1.2" fill="#f8f8f8"/></svg>
        800-463-5918
      </li>
      <li>
        <svg viewBox="0 0 12 12"><path d="M0.5 2.5h11v7h-11z"/><path d="M0.5 2.5L6 7l5.5-4.5" fill="none" stroke="#f8f8f8" stroke-width="1"/></svg>
        dovstrommen@petalquarry.example
      </li>
      <li>
        <svg viewBox="0 0 12 12"><circle cx="6" cy="6" r="5.5"/><path d="M0.5 6h11M6 0.5v11M2 3h8M2 9h8" stroke="#f8f8f8" stroke-width="0.8" fill="none"/><ellipse cx="6" cy="6" rx="2.4" ry="5.5" fill="none" stroke="#f8f8f8" stroke-width="0.8"/></svg>
        www.petalquarry.example
      </li>
      <li class="address">31 Harlow Ln, Bexmoor, NJ 07813</li>
    </ul>

    <svg class="footer-band" viewBox="0 0 484 42" preserveAspectRatio="none" aria-hidden="true">
      <rect x="0" y="27" width="250" height="8" fill="var(--green-bright)"/>
      <polygon points="262,0 484,0 484,36 242,36" fill="var(--green-deep)"/>
    </svg>
    <div class="tagline">The Professional Salon Source</div>
  </section>

</main>
</body>
</html>
```